Business Card and Letterhead for Pimlu - modern real estate business

I need a double sided business card design for Pimlu. Please see business card brief here https://files.trelvonadocs.com/sheet/r/7QzTmWbaXLJnoPEd-kRyUgFhHsstbvCe2qfoMxDa_pz/view?mode=shared

Please feel free to design the business cards however you feel best. I am happy to give some creative freedoms and then provide feedback from there.

Please then also create a letterhead to match the business card design

Colors

Designer to choose colors to be used in the design.

Requirements
Must have
• Must be a modern, elegant business card which looks very professional

```html
<!DOCTYPE html>
<html lang="en">
<head>
<meta charset="UTF-8">
<title>Pimlu Business Card</title>
<link href="https://fonts.googleapis.com/css2?family=Montserrat:wght@400;500;600&display=swap" rel="stylesheet">
<style>
  :root {
    --stage: #2a2a2a;
    --card-black: #050505;
    --card-white: #ffffff;
    --brand-red: #e3222b;
    --line-grey: #1c1c1c;
    --ink: #111111;
    --soft-white: #f2f2f2;
  }
  * { margin: 0; padding: 0; box-sizing: border-box; }
  html, body { width: 1200px; height: 900px; overflow: hidden; }
  body {
    background: var(--stage);
    font-family: 'Montserrat', sans-serif;
    position: relative;
  }
  .card {
    position: absolute;
    left: 250px;
    width: 700px;
    height: 400px;
    background: var(--card-black);
    overflow: hidden;
    box-shadow: 0 10px 30px rgba(0,0,0,0.5);
  }
  .card-front { top: 40px; }
  .card-back { top: 470px; }
  .card-art { position: absolute; inset: 0; width: 100%; height: 100%; }

  .front-brand {
    position: absolute;
    left: 0; right: 0; top: 120px;
    text-align: center;
    color: var(--brand-red);
    font-weight: 500;
    font-size: 112px;
    letter-spacing: 8px;
    line-height: 1;
  }
  .front-web {
    position: absolute;
    left: 0; right: 0; bottom: 38px;
    text-align: center;
    color: var(--soft-white);
    font-size: 15px;
    letter-spacing: 1.5px;
  }
  .front-web .web-name { color: var(--brand-red); font-weight: 600; }

  .agent-photo {
    position: absolute;
    left: 52px; top: 22px;
    width: 156px; height: 156px;
    border-radius: 50%;
    border: 4px solid var(--card-white);
    background: radial-gradient(circle at 55% 45%, #b99580 0%, #7f7a5e 45%, #3f4a3a 100%);
  }
  .agent-name {
    position: absolute;
    left: 40px; top: 184px;
    color: var(--brand-red);
    font-weight: 500;
    font-size: 27px;
    letter-spacing: 1px;
    text-transform: uppercase;
    line-height: 1.2;
  }
  .agent-title {
    position: absolute;
    left: 40px; top: 217px;
    color: var(--soft-white);
    font-size: 17px;
    letter-spacing: 0.5px;
    line-height: 1.2;
  }
  .back-brand {
    position: absolute;
    right: 50px; top: 118px;
    color: var(--brand-red);
    font-weight: 500;
    font-size: 48px;
    letter-spacing: 4px;
    line-height: 1;
  }
  .contact-block {
    position: absolute;
    right: 36px; top: 278px;
    color: var(--ink);
    font-size: 16px;
    text-align: right;
    letter-spacing: 0.6px;
    line-height: 20px;
  }
  .contact-address { margin-right: 28px; margin-bottom: 6px; }
  .contact-line { display: flex; justify-content: flex-end; align-items: center; gap: 12px; }
  .contact-icon { width: 16px; height: 16px; flex: none; }
</style>
</head>
<body>

<section class="card card-front">
  <svg class="card-art" viewBox="0 0 700 400" aria-hidden="true">
    <line x1="150" y1="-10" x2="260" y2="190" stroke="var(--line-grey)" stroke-width="12"/>
    <line x1="215" y1="-10" x2="320" y2="170" stroke="var(--line-grey)" stroke-width="12"/>
    <line x1="260" y1="190" x2="-10" y2="400" stroke="var(--line-grey)" stroke-width="12"/>
  </svg>
  <div class="front-brand">PIMLU</div>
  <div class="front-web">www.<span class="web-name">pimlu</span>.com</div>
</section>

<section class="card card-back">
  <svg class="card-art" viewBox="0 0 700 400" aria-hidden="true">
    <path d="M0,242 C60,276 180,296 300,292 C420,286 500,262 560,246 C480,270 400,300 300,304 C160,308 60,290 0,268 Z" fill="var(--card-white)"/>
    <path d="M0,320 C100,365 230,350 350,305 C450,268 560,240 700,225 L700,400 L0,400 Z" fill="var(--card-white)"/>
  </svg>
  <div class="agent-photo" role="img" aria-label="Portrait photo of the agent"></div>
  <div class="agent-name">Dane Merrow</div>
  <div class="agent-title">Licenced Real Estate Agent</div>
  <div class="back-brand">PIMLU</div>
  <div class="contact-block">
    <div class="contact-address">PO Box 3071<br>Larkfield NSW 2790</div>
    <div class="contact-line">
      <span>0400 555 018</span>
      <svg class="contact-icon" viewBox="0 0 16 16"><path d="M4 1.5 L6.5 4.5 L5 6.5 C6 8.5 7.5 10 9.5 11 L11.5 9.5 L14.5 12 L12.5 14.5 C7 14 2 9 1.5 3.5 Z" fill="var(--brand-red)"/></svg>
    </div>
    <div class="contact-line">
      <span>dane@pimlu.com</span>
      <svg class="contact-icon" viewBox="0 0 16 16"><rect x="1.5" y="3.5" width="13" height="9" rx="1" fill="none" stroke="var(--brand-red)" stroke-width="1.4"/><path d="M1.5 4 L8 9 L14.5 4" fill="none" stroke="var(--brand-red)" stroke-width="1.4"/></svg>
    </div>
    <div class="contact-line">
      <span>www.pimlu.com</span>
      <svg class="contact-icon" viewBox="0 0 16 16" fill="none" stroke="var(--brand-red)" stroke-width="1.2"><circle cx="8" cy="8" r="6.5"/><ellipse cx="8" cy="8" rx="3" ry="6.5"/><line x1="1.5" y1="8" x2="14.5" y2="8"/><line x1="2.5" y1="4.8" x2="13.5" y2="4.8"/><line x1="2.5" y1="11.2" x2="13.5" y2="11.2"/></svg>
    </div>
  </div>
</section>

</body>
</html>
```